Website for new dental office

I am Dr. Colin Ashford and am building a new dental practice. I specialize in general dentistry. I am young and have a higher end dental practice incorporating very new technologies and would like my website to reflect that. As many dental patients are older, the website must be very easy to navigate. I would like patients to be able to request appointments, and will eventually add on patient information forms (the health history, etc, that you normally fill out in the practice) from my practice management software, so leave an area for that.

Industry/Entity Type

Building

```html
<!DOCTYPE html>
<html lang="en">
<head>
<meta charset="utf-8">
<title>BrightSmile Dental</title>
<link rel="stylesheet" href="https://fonts.googleapis.com/css2?family=Open+Sans:wght@400;600;700&display=swap">
<style>
:root{
  --blue:#3f7cc6;
  --blue-dark:#2f66a9;
  --blue-text:#2b6cb8;
  --gold:#f2b21c;
  --orange:#e59a12;
  --ink:#3b3b3b;
  --muted:#8a8a8a;
  --line:#dcdcdc;
  --page:#eeeeee;
  --white:#ffffff;
}
*{box-sizing:border-box;margin:0;padding:0}
html,body{width:1200px;height:684px;overflow:hidden}
body{background:var(--page);font-family:"Open Sans",Arial,sans-serif;color:var(--ink);font-size:12px}
.site{width:1040px;height:684px;margin:0 auto;background:var(--white);display:flex;flex-direction:column}

.top-bar{height:26px;display:flex;justify-content:flex-end;align-items:center;gap:16px;padding:0 24px;font-size:10px;color:var(--muted)}
.top-bar a{color:var(--muted);text-decoration:none}

.header{height:58px;display:flex;align-items:center;justify-content:space-between;padding:0 24px}
.brand{display:flex;align-items:center;gap:8px;font-size:20px;font-weight:600;color:var(--blue-text)}
.brand-dot{width:14px;height:14px;border-radius:50%;background:var(--blue-text)}
.header-contact{display:flex;align-items:center;gap:18px}
.chat{display:flex;align-items:center;gap:8px}
.chat-avatar{width:34px;height:34px;border-radius:50%;background:linear-gradient(#e9eef4,#c7d3e0)}
.chat-text{font-size:10px;color:var(--blue-text);font-weight:600;line-height:1.3}
.chat-btn{display:inline-block;margin-top:2px;background:var(--gold);color:var(--white);padding:2px 8px;border-radius:3px;font-size:11px}
.chat-btn small{display:block;font-size:8px;font-weight:400}
.enquiries{font-size:11px;line-height:1.35;font-weight:600}
.enquiries .label{color:var(--blue-text);font-size:10px;display:flex;align-items:center;gap:4px}

.nav{height:30px;background:var(--blue);display:flex;padding:0 24px}
.nav a{color:var(--white);text-decoration:none;font-size:10px;font-weight:600;padding:0 16px;display:flex;align-items:center}
.nav a.active{background:var(--gold)}

.hero{height:170px;position:relative;background:linear-gradient(90deg,#f3f5f7 0%,#e6ebf0 45%,#dfe6ee 100%)}
.hero-photo{position:absolute;right:250px;top:0;width:340px;height:170px;background:linear-gradient(135deg,#f0d9b0 0%,#e7b84a 45%,#c9d3dd 100%);opacity:.85}
.hero-copy{position:absolute;left:60px;top:44px}
.hero-copy .kicker{font-size:22px;color:var(--blue-text);font-weight:400}
.hero-copy h1{font-size:30px;color:var(--orange);font-weight:700;letter-spacing:.5px;line-height:1.1}
.hero-copy p{font-size:13px;color:var(--ink);margin-top:4px}

.booking{height:124px;background:var(--blue);color:var(--white);position:relative}
.tabs{display:flex;height:24px}
.tab{width:320px;display:flex;align-items:center;gap:8px;padding:0 24px;font-size:13px}
.tab.alt{margin-left:auto;margin-right:150px;background:var(--white);color:var(--blue-text);width:300px;position:relative;top:-4px;height:24px}
.columns{display:flex;padding:10px 24px 0;gap:34px;font-size:10px}
.col{flex:1}
.col h3{font-size:11px;font-weight:400;display:flex;align-items:center;gap:6px;margin-bottom:6px}
.hours{width:100%;border-collapse:collapse}
.hours td{padding:3px 0;border-bottom:1px solid rgba(255,255,255,.35)}
.hours td:last-child{text-align:right}
.col p{line-height:1.45}
.btn-light{display:inline-block;background:var(--white);color:var(--blue-text);padding:2px 10px;margin-top:6px;font-size:9px}
.form{display:grid;grid-template-columns:1fr 1fr;gap:6px 10px}
.field{border:1px solid rgba(255,255,255,.8);height:17px;padding:0 5px;font-size:9px;display:flex;align-items:center}
.send{grid-column:2;justify-self:end;background:var(--white);color:var(--blue-text);padding:1px 18px;font-size:9px}

.section-head{height:50px;text-align:center;padding-top:10px}
.section-head h2{font-size:16px;font-weight:600;color:var(--blue-text)}
.section-head p{font-size:10px;color:var(--muted)}

.services{height:120px;display:flex;gap:14px;padding:0 24px}
.card{flex:1;border:1px solid var(--line);display:flex;flex-direction:column}
.card-photo{height:58px;background:linear-gradient(135deg,#eef2f6,#c9d8e8)}
.card h4{font-size:12px;color:var(--blue-text);font-weight:600;padding:6px 10px 2px}
.card p{font-size:10px;color:var(--muted);padding:0 10px}
.card .bar{margin-top:auto;height:5px;background:var(--gold)}

.bottom{height:100px;display:flex;gap:14px;padding:10px 24px 0}
.doctor,.request{border:1px solid var(--line);display:flex;gap:12px;padding:8px;flex:1}
.doctor-photo{width:70px;background:linear-gradient(#f1e6d8,#d9c3a6)}
.doctor h4,.request h4{font-size:13px;color:var(--blue-text);font-weight:600}
.doctor .role{font-size:10px;color:var(--orange);font-weight:600}
.doctor p,.request p{font-size:10px;color:var(--muted);margin-top:3px}
.request{flex-direction:column;gap:0}
.request .btn{align-self:flex-start;margin-top:8px;background:var(--blue);color:var(--white);padding:3px 14px;font-size:10px}
</style>
</head>
<body>
<div class="site">
  <div class="top-bar">
    <a href="#">Friendbook</a><a href="#">Chirper</a><a href="#">ProLink</a><a href="#">OrbitPlus</a>
  </div>

  <header class="header">
    <div class="brand"><span class="brand-dot"></span>BrightSmile Dental</div>
    <div class="header-contact">
      <div class="chat">
        <div class="chat-avatar" role="img" aria-label="Portrait of a receptionist"></div>
        <div class="chat-text">Have Questions?<br><span class="chat-btn"><small>Click here to</small>Chat Online</span></div>
      </div>
      <div class="enquiries">
        <div class="label">
          <svg width="10" height="10" viewBox="0 0 10 10"><path d="M2 1l2 2-1 1.3c.6 1.2 1.5 2.1 2.7 2.7L7 6l2 2-1.2 1.2C4.5 9 1 5.5.8 2.2z" fill="currentColor"/></svg>
          ENQUIRIES
        </div>
        Call: 555 210 48<br>Intl: +12 3 456 7892
      </div>
    </div>
  </header>

  <nav class="nav">
    <a href="#" class="active">HOME</a><a href="#">ABOUT US</a><a href="#">THE PRACTICE</a><a href="#">AREA OF EXPERTISE</a><a href="#">APPOINTMENT</a><a href="#">CONTACT</a>
  </nav>

  <section class="hero">
    <div class="hero-photo" role="img" aria-label="Smiling family of mother, father and young daughter"></div>
    <div class="hero-copy">
      <div class="kicker">We Care About</div>
      <h1>PROIN GRAVIDA NIBH</h1>
      <p>Aenean quis bibendum auctor, nisi elit</p>
    </div>
  </section>

  <section class="booking">
    <div class="tabs">
      <div class="tab">Make an Appointment</div>
      <div class="tab alt">
        <svg width="12" height="12" viewBox="0 0 12 12"><rect x="1" y="3" width="10" height="8" fill="none" stroke="currentColor"/><circle cx="6" cy="7" r="2" fill="currentColor"/></svg>
        For Emergency Cases
      </div>
    </div>
    <div class="columns">
      <div class="col">
        <h3>
          <svg width="10" height="10" viewBox="0 0 10 10"><circle cx="5" cy="5" r="4" fill="none" stroke="#fff"/><path d="M5 2.5V5h2" stroke="#fff" fill="none"/></svg>
          Working Time
        </h3>
        <table class="hours">
          <tr><td>Monday - Friday</td><td>8.00 - 17.00</td></tr>
          <tr><td>Saturday</td><td>9.30 - 17.30</td></tr>
          <tr><td>Sunday</td><td>9.30 - 15.00</td></tr>
        </table>
      </div>
      <div class="col">
        <h3>
          <svg width="10" height="10" viewBox="0 0 10 10"><rect x="1" y="2" width="8" height="7" fill="none" stroke="#fff"/><path d="M1 4h8" stroke="#fff"/></svg>
          Doctors Timetable
        </h3>
        <p>Lorem ipsum dolor sit amet, consectetur adipisicing elit, sed do eiusmod tempor incididunt ut labore et dolore.</p>
        <span class="btn-light">View Timetable</span>
      </div>
      <div class="col">
        <h3>
          <svg width="10" height="10" viewBox="0 0 10 10"><rect x="1" y="2" width="8" height="7" fill="none" stroke="#fff"/><path d="M3 1v2M7 1v2" stroke="#fff"/></svg>
          Booking a Visit
        </h3>
        <div class="form">
          <div class="field">Select Department</div>
          <div class="field">Your Phone</div>
          <div class="field">Full Name</div>
          <div class="field">mm/dd/yyyy</div>
          <div class="send">Send</div>
        </div>
      </div>
    </div>
  </section>

  <section class="section-head">
    <h2>Proin Gravida Nibh Auctor</h2>
    <p>Aenean sollicitudin, lorem quis bibendum auctor, nisi elit consequat</p>
  </section>

  <section class="services">
    <article class="card"><div class="card-photo" role="img" aria-label="Patient in the dental chair"></div><h4>Gentle Cleaning</h4><p>Modern care for the whole family.</p><div class="bar"></div></article>
    <article class="card"><div class="card-photo" role="img" aria-label="Dentist with dental instruments"></div><h4>Digital X-Rays</h4><p>Modern care for the whole family.</p><div class="bar"></div></article>
    <article class="card"><div class="card-photo" role="img" aria-label="Smiling patient after treatment"></div><h4>Teeth Whitening</h4><p>Modern care for the whole family.</p><div class="bar"></div></article>
    <article class="card"><div class="card-photo" role="img" aria-label="Woman with a bright smile"></div><h4>Dental Implants</h4><p>Modern care for the whole family.</p><div class="bar"></div></article>
  </section>

  <section class="bottom">
    <div class="doctor">
      <div class="doctor-photo" role="img" aria-label="Portrait of the dentist"></div>
      <div>
        <h4>Dr. Colin Ashford</h4>
        <div class="role">General Dentist</div>
        <p>Calm, modern treatment using the newest technology.</p>
      </div>
    </div>
    <div class="request">
      <h4>Make an Appointment</h4>
      <p>Request a visit online in a few steps.</p>
      <span class="btn">Book Now</span>
    </div>
  </section>
</div>
</body>
</html>
```